Modern business card design for professional copywriter

I'd like a business card design that I can use to have my cards printed out by quillprint.com as a squared corners business card (see artwork and design guidelines here: https://help.quillprint.com/hc/en-gb/sections/200570950-QUILL-Product-Templates)

The design should be clean and modern and reflect the colours, tone and branding on my website: https://tessavorrin.com.au

Target Market(s)

Professionals, B2B small business owners

Industry/Entity Type

Business

Contact Information for Business Card

Tessa Vorrin
m: 0468 905 327
e: tessa@tessavorrin.com.au
w: tessavorrin.com.au

Font styles to use
Sans Serif

Requirements
Must have
• Tagline: "Smart copywriting for clever business people"
• Brand colours: fd8000, 009984, 666666 and black
Nice to have

```html
<!DOCTYPE html>
<html lang="en">
<head>
<meta charset="utf-8">
<title>Tessa Vorrin — Business Card</title>
<link rel="stylesheet" href="https://fonts.googleapis.com/css2?family=Open+Sans:wght@400;600;700&display=swap">
<style>
  :root {
    --orange: #fd8000;
    --teal: #009984;
    --grey: #666666;
    --charcoal: #3c3d3d;
    --black: #000000;
    --card: #ffffff;
    --backdrop: #e9e9e9;
    --ring: #bdbdbd;
  }
  * { box-sizing: border-box; margin: 0; padding: 0; }
  html, body { width: 1200px; height: 533px; overflow: hidden; }
  body {
    background: var(--backdrop);
    font-family: "Open Sans", Arial, sans-serif;
    position: relative;
  }
  .card {
    position: absolute;
    top: 84px;
    width: 549px;
    height: 313px;
    background: var(--card);
    overflow: hidden;
  }
  .card--front { left: 60px; }
  .card--back { left: 620px; }

  .edge-tab {
    position: absolute;
    left: 0;
    top: 40px;
    width: 37px;
    height: 236px;
    background: var(--charcoal);
    border-radius: 0 10px 10px 0;
  }
  .dark-panel {
    position: absolute;
    right: 0;
    top: 40px;
    height: 236px;
    background: var(--charcoal);
    border-radius: 14px 0 0 14px;
    display: flex;
    align-items: center;
    justify-content: center;
  }
  .card--front .dark-panel { width: 274px; }
  .card--back .dark-panel { width: 235px; padding: 0 10px 0 6px; }

  .identity { position: absolute; left: 48px; top: 34px; }
  .identity__name {
    font-size: 14.5px;
    font-weight: 700;
    color: var(--teal);
    letter-spacing: 0.2px;
  }
  .identity__name .first { color: var(--orange); }
  .identity__role {
    font-size: 8.5px;
    font-weight: 600;
    color: var(--black);
    margin-top: 1px;
  }

  .contact-list { list-style: none; }
  .contact-list__item {
    position: absolute;
    left: 11px;
    display: flex;
    align-items: center;
    gap: 15px;
  }
  .contact-list__item:nth-child(1) { top: 108px; }
  .contact-list__item:nth-child(2) { top: 148px; }
  .contact-list__item:nth-child(3) { top: 188px; }
  .contact-list__badge {
    width: 17px;
    height: 17px;
    border-radius: 50%;
    background: var(--card);
    border: 1.5px solid var(--ring);
    color: var(--orange);
    font-size: 8px;
    font-weight: 700;
    display: flex;
    align-items: center;
    justify-content: center;
  }
  .contact-list__text {
    font-size: 9.5px;
    font-weight: 600;
    color: var(--orange);
    letter-spacing: 0.2px;
  }

  .wordmark {
    font-size: 35px;
    font-weight: 600;
    letter-spacing: -0.5px;
    white-space: nowrap;
  }
  .wordmark--on-dark { color: var(--orange); }
  .wordmark--on-light {
    position: absolute;
    left: 80px;
    top: 134px;
    color: var(--teal);
  }
  .tagline {
    font-size: 7.6px;
    font-weight: 700;
    color: var(--orange);
    text-transform: uppercase;
    white-space: nowrap;
    letter-spacing: 0;
  }
</style>
</head>
<body>
  <section class="card card--front" aria-label="Business card front">
    <div class="edge-tab"></div>
    <div class="identity">
      <p class="identity__name"><span class="first">TESSA</span> VORRIN</p>
      <p class="identity__role">COPYWRITER</p>
    </div>
    <ul class="contact-list">
      <li class="contact-list__item"><span class="contact-list__badge">M</span><span class="contact-list__text">0468 905 327</span></li>
      <li class="contact-list__item"><span class="contact-list__badge">E</span><span class="contact-list__text">TESSA@TESSAVORRIN.COM.AU</span></li>
      <li class="contact-list__item"><span class="contact-list__badge">W</span><span class="contact-list__text">TESSAVORRIN.COM.AU</span></li>
    </ul>
    <div class="dark-panel">
      <span class="wordmark wordmark--on-dark">Tessa Vorrin</span>
    </div>
  </section>

  <section class="card card--back" aria-label="Business card back">
    <div class="edge-tab"></div>
    <span class="wordmark wordmark--on-light">Tessa Vorrin</span>
    <div class="dark-panel">
      <p class="tagline">Smart copywriting for clever business people</p>
    </div>
  </section>
</body>
</html>
```